Business card for Crestline Bathrooms

Please design a business card for our bathroom renovation business. You can use my existing logo, but if you have an idea to modernize it, I would like to see it. Please see attached files first. I would like to use the blue and the orange theme. I like the concept of using the shower head in the logo. Please find following a design (or two) that I have been trying to create with my limited resources. That design was for a sign, but I was going to adopt it and use it as a business card as well. I like the concept of the water splash but I don’t think it “flows” nicely together with the logo. Another thought is that maybe creating the logo out of water splash could work and have a dramatic effect (like the water text and the butterfly picture attached with similar background instead of white). If the above doesn’t work I would like to see a modern simplified design. One of the attached files named as the unwanted business card has all the details that I want included in the business card. Please note that it is two sided.
Updates

I am very thankful for the designs that I have received, but they are very similar and only a couple of attempts to do something with the water splash as per my original brief. Modernizing the logo and having it made out of out of water splash with the orange as color accent could work and have a dramatic effect (like the water text and the butterfly picture attached with similar background instead of white). Please do not use the butterfly itself! This is just an example that images can be created out of water splash.

Contact Information for Business Card

all the details are on the unwonted business card file included

Colors
3176b5

Requirements
Nice to have
• Copied from the brief:
• ... maybe creating the logo out of water splash could work and have a dramatic effect (like the water text and the butterfly picture attached with similar background instead of white). Please do not use the butterfly itself!
Should not have
• I am getting designs with a butterfly. The butterfly picture was an example of creating something from a water splash. The butterfly itself has no association with anything other than the concept of creating a logo out of water splash. Sorry, I thought I was clear in the brief.

```html
<!DOCTYPE html>
<html lang="en">
<head>
<meta charset="utf-8">
<title>Crestline Bathrooms – Business Card</title>
<link href="https://fonts.googleapis.com/css2?family=Roboto:wght@400;500;700&display=swap" rel="stylesheet">
<style>
  :root {
    --coral: #ea7767;
    --coral-light: #f08f7f;
    --navy: #1c4a7c;
    --white: #ffffff;
    --lavender: #c9c3e2;
    --lavender-soft: #e6e1f1;
    --stage: #2b2b2d;
  }
  * { box-sizing: border-box; margin: 0; padding: 0; }
  html, body { width: 1200px; height: 886px; overflow: hidden; }
  body {
    background: var(--stage);
    font-family: "Roboto", Arial, sans-serif;
    position: relative;
  }
  .card {
    position: absolute;
    width: 520px;
    height: 318px;
    border-radius: 18px;
    overflow: hidden;
    top: 284px;
  }
  /* Back side */
  .card-back {
    left: 50px;
    background: var(--coral);
    color: var(--white);
    text-align: center;
  }
  .card-back .brand {
    position: absolute;
    top: 58px; left: 0; right: 0;
    display: flex; justify-content: center; align-items: center; gap: 10px;
    font-size: 30px; font-weight: 700; color: var(--navy);
  }
  .brand-dot {
    width: 14px; height: 14px; border-radius: 50%; background: var(--navy);
  }
  .card-back .taglines {
    position: absolute;
    top: 130px; left: 0; right: 0;
    list-style: none;
    font-size: 13.5px; line-height: 19px; font-weight: 400;
  }
  .card-back .badges {
    position: absolute;
    top: 232px; left: 0; right: 0;
    display: flex; justify-content: center; align-items: center; gap: 18px;
  }
  .badge-round { width: 30px; height: 30px; border-radius: 8px; background: var(--white); }
  .badge-divider { width: 1px; height: 30px; background: rgba(255,255,255,0.7); }
  .badge-wide { width: 96px; height: 22px; border-radius: 3px; background: var(--white); }

  /* Front side */
  .card-front { left: 630px; background: var(--white); }
  .card-front svg.art { position: absolute; inset: 0; }
  .card-front .brand {
    position: absolute;
    top: 52px; left: 30px;
    display: flex; align-items: center; gap: 9px;
    font-size: 26px; font-weight: 700; color: var(--navy);
  }
  .card-front .holder {
    position: absolute;
    top: 100px; right: 34px;
    font-size: 19px; font-weight: 700; color: var(--navy);
    letter-spacing: 0.3px;
  }
  .contact {
    position: absolute;
    left: 34px; top: 196px;
    color: var(--white);
    font-size: 13.5px; line-height: 18px;
  }
  .contact .address { margin-bottom: 6px; }
  .contact ul { list-style: none; }
  .contact li { display: flex; align-items: center; gap: 8px; }
  .contact li svg { width: 12px; height: 12px; flex: none; }
  .contact .web { padding-left: 20px; }
</style>
</head>
<body>

  <section class="card card-back" aria-label="Business card, back">
    <div class="brand"><span class="brand-dot"></span>Crestline Bathrooms</div>
    <ul class="taglines">
      <li>Complete Bathroom Renovations &amp; Remodelling</li>
      <li>Highly Skilled &amp; Qualified Tradespeople</li>
      <li>Professional Service From Concept To Completion</li>
      <li>All Work Guaranteed</li>
    </ul>
    <div class="badges">
      <span class="badge-round" role="img" aria-label="Industry association membership badge"></span>
      <span class="badge-divider"></span>
      <span class="badge-wide" role="img" aria-label="Builders association membership badge"></span>
    </div>
  </section>

  <section class="card card-front" aria-label="Business card, front">
    <svg class="art" viewBox="0 0 520 318" width="520" height="318">
      <defs>
        <linearGradient id="splash-tone" x1="0" y1="0" x2="1" y2="0.3">
          <stop offset="0.28" stop-color="#ffffff"/>
          <stop offset="0.55" stop-color="#e6e1f1"/>
          <stop offset="1" stop-color="#c3bde0"/>
        </linearGradient>
        <linearGradient id="wave-tone" x1="0" y1="1" x2="1" y2="0">
          <stop offset="0" stop-color="#ea7767"/>
          <stop offset="0.6" stop-color="#f08f7f"/>
          <stop offset="1" stop-color="#ea7767"/>
        </linearGradient>
      </defs>
      <rect width="520" height="318" fill="url(#splash-tone)" role="img" aria-label="Photograph of a clear water splash with droplets on a soft lavender background"/>
      <path d="M0 205 C130 202 200 125 300 114 C400 104 465 150 520 178 L520 318 L0 318 Z" fill="url(#wave-tone)"/>
    </svg>

    <div class="brand"><span class="brand-dot"></span>Crestline Bathrooms</div>
    <div class="holder">DANIEL HARWICK</div>

    <div class="contact">
      <p class="address">PO Box 41<br>Larchmont 2710</p>
      <ul>
        <li>
          <svg viewBox="0 0 24 24" aria-hidden="true"><path fill="#1c4a7c" d="M6.6 10.8a15 15 0 0 0 6.6 6.6l2.2-2.2a1 1 0 0 1 1-.25 11.4 11.4 0 0 0 3.6.57 1 1 0 0 1 1 1V20a1 1 0 0 1-1 1A17 17 0 0 1 3 4a1 1 0 0 1 1-1h3.5a1 1 0 0 1 1 1c0 1.25.2 2.45.57 3.6a1 1 0 0 1-.25 1z"/></svg>
          0400 555 218
        </li>
        <li>
          <svg viewBox="0 0 24 24" aria-hidden="true"><rect x="6" y="2" width="12" height="20" rx="2" fill="none" stroke="#1c4a7c" stroke-width="2.5"/></svg>
          5550 1942
        </li>
        <li>
          <svg viewBox="0 0 24 24" aria-hidden="true"><rect x="2" y="5" width="20" height="14" rx="1.5" fill="#1c4a7c"/><path d="M3 6l9 7 9-7" fill="none" stroke="#ea7767" stroke-width="1.8"/></svg>
          daniel@crestlinebathrooms.com.au
        </li>
        <li class="web">www.crestlinebathrooms.com.au</li>
      </ul>
    </div>
  </section>

</body>
</html>
```